New web design for a service provider in the medical field

We are looking for a new design for our website. We are a company that repairs and sells medical endoscopes. Our customers include doctors and hospitals. Our current website can be found at https://lumavex.de/en/lumavex-english.
We need a new web design (without programming) for the following 3 pages:
-Startpage https://lumavex.de/en/lumavex-english/
-Used endoscopes https://lumavex.de/en/used-endoscopes/
-Purchase https://lumavex.de/en/purchase/
The design should be modern and stylish.
The blue color of the logo should be reflected on the page, but not too intrusive.
I have uploaded the images from the header. If more images are needed, let me know and I will upload them.

Target Market(s)
Doctors and hospitals

```html
<!DOCTYPE html>
<html lang="en">
<head>
<meta charset="utf-8">
<title>Lumavex – Endoscope Repair</title>
<link href="https://fonts.googleapis.com/css2?family=Montserrat:wght@400;500;600;700;800&family=Quicksand:wght@400;500;600;700&display=swap" rel="stylesheet">
<style>
:root{
  --blue:#2aa4e2;
  --blue-dark:#1b8fd0;
  --navy:#1c2b3c;
  --navy-2:#22364b;
  --ink:#1f2b3a;
  --muted:#4a5563;
  --light:#eef3f7;
  --white:#ffffff;
  --red:#e8261b;
  --royal:#0a4f9a;
}
*{box-sizing:border-box;margin:0;padding:0}
html,body{width:1200px;height:4992px;overflow:hidden}
body{position:relative;background:var(--white);font-family:'Quicksand',sans-serif;color:var(--ink)}
.abs{position:absolute}
h1,h2,h3,h4{font-family:'Montserrat',sans-serif}
.btn{position:absolute;display:flex;align-items:center;justify-content:center;border-radius:22px;background:var(--blue);color:var(--white);font-family:'Montserrat',sans-serif;font-weight:600;font-size:12px;letter-spacing:.3px;text-decoration:none}
.btn.dark{background:var(--navy)}
.brand{font-family:'Quicksand',sans-serif;font-weight:700;color:var(--navy);font-size:26px;display:flex;align-items:center;gap:8px}
.brand .dot{width:14px;height:14px;border-radius:50%;background:var(--blue)}
.tagline{font-size:10px;color:var(--blue);font-weight:600}

/* header */
.topbar{left:688px;top:0;width:512px;height:35px;background:var(--blue);display:flex;align-items:center;gap:26px;padding-left:24px;color:var(--white);font-family:'Montserrat',sans-serif;font-size:11px;font-weight:600}
.topbar span{display:flex;align-items:center;gap:7px}
.topbar svg{width:18px;height:18px}
.nav{left:305px;top:62px;display:flex;gap:0;font-family:'Montserrat',sans-serif;font-size:11px;font-weight:700;color:var(--ink)}
.nav a{position:absolute;white-space:nowrap;color:var(--ink);text-decoration:none}
.nav a.active::after{content:"";position:absolute;left:0;right:0;bottom:-8px;height:2px;background:var(--blue)}

/* hero */
.hero-bg{left:0;top:107px;width:1200px;height:600px;background:linear-gradient(100deg,#f4f5f6 0%,#eceef0 45%,#dfe3e6 100%)}
.hero-photo{left:520px;top:107px;width:680px;height:560px;background:radial-gradient(ellipse at 60% 45%,#ffffff 0%,#e3e6e9 45%,#c9cdd1 70%,#eef0f2 100%)}
.hero-kicker{left:105px;top:276px;font-family:'Quicksand',sans-serif;font-weight:500;font-size:27px;color:var(--blue)}
.hero-title{left:105px;top:311px;font-size:36px;font-weight:800;line-height:42px;color:var(--ink)}

/* intro */
.section-title{left:0;width:1200px;text-align:center;font-weight:800;color:var(--ink)}
.section-title em{font-style:normal;color:var(--blue)}
.intro-text{left:240px;top:903px;width:720px;text-align:center;font-size:18px;line-height:27px;color:var(--muted)}
.vline{left:601px;top:1008px;width:1px;height:68px;background:var(--blue)}

/* about */
.about-photo{left:110px;top:1136px;width:396px;height:359px;background:linear-gradient(135deg,#bfc3c7 0%,#6e7378 40%,#2a2d30 70%,#9ea3a7 100%)}
.about-h{left:607px;top:1136px;width:470px;font-size:23px;font-weight:500;line-height:31px;color:var(--ink)}
.about-p{left:609px;width:515px;font-size:13px;line-height:23px;color:var(--muted)}
.maker{position:absolute;top:1452px;width:149px;height:43px}

/* service cards */
.card{position:absolute;top:1596px;width:324px;height:351px;border:2px solid var(--blue);background:var(--white);padding:0 0 0 40px}
.card.dark{background:var(--navy);border-color:var(--navy);color:var(--white)}
.card .ico{position:absolute;left:37px;top:23px;width:78px;height:78px;border-radius:50%;background:var(--blue);display:flex;align-items:center;justify-content:center}
.card h3{position:absolute;left:40px;top:121px;font-size:22px;font-weight:700}
.card .sub{position:absolute;left:40px;top:152px;font-size:17px;font-weight:500}
.card p{position:absolute;left:40px;top:184px;width:260px;font-size:12px;line-height:18px}
.card .btn{left:37px;top:273px;width:144px;height:37px;font-size:11px}

/* faulty */
.faulty-bg{left:0;top:2040px;width:1200px;height:535px;background:linear-gradient(90deg,#eef3f8 0%,#e6eff7 45%,#cfe6f6 60%,#2a9be0 85%,#1f8bd6 100%)}
.faulty-photo{left:605px;top:2121px;width:454px;height:360px;background:radial-gradient(ellipse at 60% 50%,#4a3f3a 0%,#8d8580 30%,#e9eaeb 60%,#f6f7f8 100%);border:12px solid var(--white)}
.faulty-h{left:122px;top:2170px;font-size:30px;font-weight:800;color:var(--ink)}
.faulty-h em{font-style:normal;color:var(--blue)}
.faulty-sub{left:123px;top:2238px;font-size:22px;font-weight:500}
.faulty-p{left:123px;top:2280px;width:415px;font-size:15px;line-height:25px;color:var(--muted)}

/* benefits */
.benefit{position:absolute;width:260px}
.benefit .ring{position:absolute;left:0;top:0;width:92px;height:92px;border-radius:50%;border:2px solid var(--blue);display:flex;align-items:center;justify-content:center}
.benefit .ring i{width:76px;height:76px;border-radius:50%;background:var(--navy);display:flex;align-items:center;justify-content:center}
.benefit h4{position:absolute;left:14px;top:112px;font-size:17px;font-weight:700;line-height:20px}
.benefit p{position:absolute;left:14px;width:240px;font-size:14px;line-height:20px;color:var(--muted)}

/* decision */
.decision-h{left:0;top:3350px;width:1200px;text-align:center;font-size:26px;line-height:32px;font-weight:700;color:var(--white)}
.tile{position:absolute;width:281px;height:202px;border:1px solid rgba(255,255,255,.55);color:var(--white);padding:0 30px}
.tile.hl{background:linear-gradient(135deg,#2aa4e2,#1f93d8);border-color:var(--blue)}
.tile .ti{position:absolute;left:30px;top:20px;width:62px;height:62px;border-radius:50%;border:2px solid var(--white);display:flex;align-items:center;justify-content:center}
.tile h4{position:absolute;left:30px;top:100px;font-size:14px;font-weight:700}
.tile p{position:absolute;left:30px;top:123px;width:225px;font-size:10px;line-height:16px;opacity:.85}

/* contact */
.contact-photo{left:0;top:4023px;width:1200px;height:620px;background:linear-gradient(90deg,#c8d0d4 0%,#dfe4e6 25%,#eef0f1 45%,#ffffff 58%,#ffffff 100%)}
.help-h{left:661px;top:4193px;font-size:28px;font-weight:800;color:var(--ink)}
.help-h em{font-style:normal;color:var(--blue)}
.field{position:absolute;left:665px;width:419px;border:1px solid #b9c2cb;background:var(--white);display:flex;align-items:center;gap:10px;padding-left:18px;font-size:12px;font-weight:700;color:var(--ink)}
.field svg{width:14px;height:14px}

/* footer */
.footer{left:0;top:4643px;width:1200px;height:349px;background:var(--blue);color:var(--white)}
.f-col{position:absolute;top:70px}
.f-col h5{font-family:'Montserrat',sans-serif;font-size:13px;font-weight:700;margin-bottom:18px}
.f-col a{display:block;color:var(--white);text-decoration:none;font-size:13px;line-height:29px}
.f-div{position:absolute;top:40px;width:1px;height:230px;background:rgba(255,255,255,.35)}
.social{display:flex;gap:8px}
.social i{width:27px;height:27px;border-radius:50%;background:var(--white);display:block}
</style>
</head>
<body>

<!-- header -->
<div class="abs" style="left:100px;top:14px">
  <div class="brand">Lumavex<span class="dot"></span></div>
  <div class="tagline" style="margin-top:2px">Precision care for every scope</div>
</div>
<div class="abs topbar">
  <span><svg viewBox="0 0 18 18"><circle cx="9" cy="9" r="9" fill="#fff"/><rect x="4.5" y="6" width="9" height="6.5" fill="none" stroke="#2aa4e2" stroke-width="1.3"/><path d="M4.5 6 9 9.5 13.5 6" fill="none" stroke="#2aa4e2" stroke-width="1.3"/></svg>info@lumavex.de</span>
  <span><svg viewBox="0 0 18 18"><circle cx="9" cy="9" r="9" fill="#fff"/><path d="M6 4.5c-1 .5-1.5 1.5-1 3 .8 2.5 3 4.8 5.5 5.6 1.5.5 2.5 0 3-1l-1.8-1.6-1.2.8c-1.2-.6-2.2-1.6-2.8-2.8l.8-1.2z" fill="#2aa4e2"/></svg>+49 4030 551 720-0</span>
  <span>ENG <svg viewBox="0 0 18 18" style="width:10px;height:10px"><path d="M3 6l6 6 6-6" fill="none" stroke="#fff" stroke-width="2.5"/></svg></span>
</div>
<nav class="abs nav" style="left:0;top:63px">
  <a class="active" style="left:305px">ENDOSCOPE REPAIR</a>
  <a style="left:460px">ENDOSCOPY SYSTEMS</a>
  <a style="left:628px">ENDOSCOPY ACCESSORIES</a>
  <a style="left:826px">ACCESSORIES CATALOG</a>
  <a style="left:1016px">PURCHASE</a>
</nav>

<!-- hero -->
<div class="abs hero-bg"></div>
<div class="abs hero-photo" role="img" aria-label="Photo of flexible endoscope control bodies hanging in a white storage cabinet"></div>
<svg class="abs" style="left:0;top:590px" width="1200" height="170" viewBox="0 0 1200 170">
  <polygon points="0,22 600,105 1200,40 1200,170 0,170" fill="#fff"/>
  <polygon points="0,22 600,100 1200,28 1200,40 600,110 0,36" fill="#2aa4e2"/>
  <circle cx="600" cy="118" r="37" fill="#fff" stroke="#2aa4e2" stroke-width="2"/>
  <path d="M600 102v30M590 122l10 10 10-10" fill="none" stroke="#2aa4e2" stroke-width="2.5" stroke-linecap="round"/>
</svg>
<div class="abs hero-kicker">WELCOME TO LUMAVEX</div>
<h1 class="abs hero-title">PUT YOUR ENDOSCOPE<br>IN RELIABLE HANDS!</h1>
<a class="btn" style="left:105px;top:419px;width:163px;height:42px">LEARN MORE</a>

<!-- intro -->
<h2 class="abs section-title" style="top:810px;font-size:36px">YOUR FUTURE OUR SERVICE</h2>
<p class="abs intro-text">Lumavex GmbH is specialised in the repair and sale of Aurelo, Pendrix and Fuvion flexible medical endoscopes. As a service-oriented company, we are at your side with our knowledge and skills!</p>
<div class="abs vline"></div>

<!-- about -->
<svg class="abs" style="left:92px;top:1120px" width="420" height="360"><path d="M2 358V2h414" fill="none" stroke="#2aa4e2" stroke-width="4"/></svg>
<div class="abs about-photo" role="img" aria-label="Close-up photo of an endoscope control head with angulation wheels"></div>
<h2 class="abs about-h">Endoscope repairs and second hand endoscopes from Lumavex cause the outcome matters!</h2>
<p class="abs about-p" style="top:1243px">Lumavex is a privileged partner for the start-up facility or optimisation of existing healthcare facilities, doctor's offices and hospitals. The quality and reliability of our products and our offered service are our best advertisement!</p>
<p class="abs about-p" style="top:1346px">As a result of optimised processes and highly qualified specialists in our company, we can work very quickly and with high quality for your benefit of least possible restrictions in your doctor's office or in your hospital.</p>
<div class="maker" style="left:611px;background:var(--royal)"></div>
<div class="maker" style="left:776px;background:var(--red)"></div>
<div class="maker" style="left:942px;background:#000"></div>

<!-- service cards -->
<div class="card" style="left:99px">
  <div class="ico"><svg width="42" height="42" viewBox="0 0 42 42" fill="none" stroke="#fff" stroke-width="2"><circle cx="14" cy="21" r="9"/><circle cx="14" cy="21" r="4"/><path d="M14 12h20v18H14M34 16h4v10h-4"/></svg></div>
  <h3>REPAIR</h3><div class="sub">Endoscope repair service</div>
  <p>Manufacturer-independent we repair and maintain endoscopes, individual components</p>
  <a class="btn">REPAIR REQUEST</a>
</div>
<div class="card dark" style="left:444px">
  <div class="ico"><svg width="42" height="42" viewBox="0 0 42 42" fill="none" stroke="#fff" stroke-width="2"><path d="M12 8c6 0 8 4 8 10v16M12 8c-4 0-5 4-3 7M20 18h7v7h-7M24 25v6"/></svg></div>
  <h3>SALE</h3><div class="sub">Used endoscopes</div>
  <p>Our regular stock includes refurbished gastroscopes, colonoscopes, bronchoscopes, cystoscopes and duodenoscopes from the well-known manufacturers Aurelo, Pendrix and Fuvion.</p>
  <a class="btn" style="top:291px">PURCHSE REQUEST</a>
</div>
<div class="card" style="left:787px">
  <div class="ico"><svg width="42" height="42" viewBox="0 0 42 42" fill="none" stroke="#fff" stroke-width="2"><rect x="13" y="9" width="14" height="16" rx="3"/><path d="M20 25v10M16 14h8M27 16h5v6h-5"/></svg></div>
  <h3>PURCHASE</h3><div class="sub">Used endoscopes</div>
  <p>We are very interested in buying your old endoscopes – even defective and dismantled! We offer fair conditions! Please contact us for a purchase offer!</p>
  <a class="btn" style="top:267px">SELL DEVICE</a>
</div>

<!-- faulty -->
<div class="abs faulty-bg" role="img" aria-label="Soft blue abstract molecular background"></div>
<svg class="abs" style="left:591px;top:2103px" width="460" height="370"><path d="M2 368V2h456" fill="none" stroke="#2aa4e2" stroke-width="4"/></svg>
<div class="abs faulty-photo" role="img" aria-label="Photo of a dark flexible endoscope with its insertion tube curled"></div>
<h2 class="abs faulty-h">FAULTY <em>ENDOSCOPE?</em></h2>
<div class="abs faulty-sub">We ensure quick and smooth repairs!</div>
<p class="abs faulty-p">Lorem ipsum dolor sit amet, consectetur adipiscing elit, sed do eiusmod tempor incididunt ut labore et dolore magna aliqua. Ut enim ad minim veniam, quis nostrud exercitation ullamco laboris n</p>
<a class="btn dark" style="left:124px;top:2404px;width:151px;height:39px">PICK UP ORDER</a>

<!-- benefits -->
<h2 class="abs section-title" style="top:2642px;font-size:30px">CAUSE THE <em>OUTCOME MATTERS</em></h2>
<div class="abs" style="left:565px;top:2690px;width:70px;height:2px;background:#c9d3dc"></div>
<svg class="abs" style="left:200px;top:2770px" width="920" height="270" fill="none" stroke="#2aa4e2" stroke-width="1.5">
  <path d="M50 12H280M375 12H610M705 12H820a90 90 0 0 1 90 90v50a90 90 0 0 1-90 90H705M610 260H375M280 260H50"/>
</svg>
<div class="benefit" style="left:156px;top:2736px">
  <div class="ring"><i><svg width="40" height="40" viewBox="0 0 40 40" fill="none" stroke="#fff" stroke-width="1.8"><circle cx="20" cy="20" r="6"/><circle cx="20" cy="6" r="3"/><circle cx="20" cy="34" r="3"/><circle cx="7" cy="20" r="3"/><circle cx="33" cy="20" r="3"/><path d="M20 9v5M20 26v5M10 20h4M26 20h4"/></svg></i></div>
  <h4>One company for<br>everyone</h4><p style="top:158px">We are a service provider for doctors and hospitals!</p>
</div>
<div class="benefit" style="left:481px;top:2736px">
  <div class="ring"><i><svg width="40" height="40" viewBox="0 0 40 40" fill="none" stroke="#fff" stroke-width="1.8"><circle cx="13" cy="17" r="5"/><circle cx="27" cy="17" r="5"/><path d="M4 32c0-6 4-9 9-9s9 3 9 9M18 32c0-6 4-9 9-9s9 3 9 9"/></svg></i></div>
  <h4>Experience<br>characterises us</h4><p style="top:158px">Our team has many years of experience in the business field!</p>
</div>
<div class="benefit" style="left:811px;top:2736px">
  <div class="ring"><i><svg width="40" height="40" viewBox="0 0 40 40" fill="none" stroke="#fff" stroke-width="1.8"><rect x="13" y="6" width="14" height="16" rx="3"/><path d="M20 22v12M17 12h6M27 13h5v6h-5"/></svg></i></div>
  <h4>The product is close<br>to our hearts</h4><p style="top:158px">We repair and sell second hand, flexible endoscopes!</p>
</div>
<div class="benefit" style="left:156px;top:2984px">
  <div class="ring"><i><svg width="40" height="40" viewBox="0 0 40 40" fill="none" stroke="#fff" stroke-width="1.8"><path d="M20 5l12 5v9c0 8-5 13-12 16-7-3-12-8-12-16v-9z"/><path d="M14 20l4 4 8-8"/></svg></i></div>
  <h4 style="left:24px;top:108px">Guaranteed service</h4><p style="left:24px;top:134px">You receive a six-month warranty on all repairs!</p>
</div>
<div class="benefit" style="left:481px;top:2984px">
  <div class="ring"><i><svg width="40" height="40" viewBox="0 0 40 40" fill="none" stroke="#fff" stroke-width="1.8"><path d="M20 6l2.5 5 5.5.8-4 3.9 1 5.5-5-2.6-5 2.6 1-5.5-4-3.9 5.5-.8z"/><path d="M5 28h6l8 3h8l6-4M11 26v9"/></svg></i></div>
  <h4 style="left:10px;top:108px">Quality not quantity</h4><p style="left:10px;top:134px">Reliability and durability instead of inferior replacements!</p>
</div>
<div class="benefit" style="left:811px;top:2984px">
  <div class="ring"><i><svg width="40" height="40" viewBox="0 0 40 40" fill="none" stroke="#fff" stroke-width="1.8"><path d="M18 5l11 5v8c0 7-4 12-11 15-7-3-11-8-11-15v-8z"/><path d="M13 18l4 4 6-6"/><circle cx="29" cy="29" r="5"/></svg></i></div>
  <h4 style="left:18px;top:108px">Services for everyone</h4><p style="left:18px;top:134px">Our service includes the manufacturers Aurelo, Pendrix and Fuvion!</p>
</div>

<!-- decision -->
<svg class="abs" style="left:0;top:3225px" width="1200" height="900">
  <polygon points="0,75 310,0 1200,82 1200,795 880,795 450,885 0,795" fill="#1c2b3c"/>
  <polygon points="0,75 310,0 1200,82 1200,92 310,10 0,87" fill="#2aa4e2"/>
  <polygon points="0,797 450,887 880,797 1200,797 1200,809 880,809 450,900 0,809" fill="#2aa4e2"/>
</svg>
<h2 class="abs decision-h">LUMAVEX GMBH, YOUR DECISION<br>FOR YOUR FUTURE</h2>
<div class="tile" style="left:161px;top:3463px"><div class="ti"><svg width="30" height="30" viewBox="0 0 30 30" fill="none" stroke="#fff" stroke-width="1.8"><path d="M6 24L18 12M20 6a5 5 0 0 0 4 8M6 6l18 18"/></svg></div><h4>Fast Repairs</h4><p style="top:118px">Keep potential disruptions in your doctor's office or in your hospital at minimum</p></div>
<div class="tile hl" style="left:458px;top:3463px"><div class="ti"><svg width="30" height="30" viewBox="0 0 30 30" fill="none" stroke="#fff" stroke-width="1.8"><circle cx="15" cy="13" r="7"/><path d="M15 9v8M6 26h18"/></svg></div><h4 style="top:108px">Highly cost efficient</h4><p style="top:131px">Benefit from our first class recommendations and implementation by our experienced staff.</p></div>
<div class="tile" style="left:748px;top:3463px"><div class="ti"><svg width="30" height="30" viewBox="0 0 30 30" fill="none" stroke="#fff" stroke-width="1.8"><circle cx="12" cy="17" r="6"/><circle cx="21" cy="10" r="4"/></svg></div><h4>On-site service</h4><p>We will gladly pay you a visit to to carry out analysis and repairs on site. Due to our many years of experience</p></div>
<div class="tile" style="left:161px;top:3676px"><div class="ti"><svg width="30" height="30" viewBox="0 0 30 30" fill="none" stroke="#fff" stroke-width="1.8"><path d="M8 24c0-8 3-12 7-12s7 4 7 12zM12 12l-2-6h10l-2 6"/></svg></div><h4>Loan equipment service</h4><p>We will gladly pay you a visit to to carry out analysis and repairs on site. Due to our many years of experience</p></div>
<div class="tile" style="left:458px;top:3676px"><div class="ti"><svg width="30" height="30" viewBox="0 0 30 30" fill="none" stroke="#fff" stroke-width="1.8"><rect x="8" y="6" width="14" height="18"/><path d="M11 11h8M11 15h8M11 19h5"/></svg></div><h4 style="top:112px">Without a maintenance contract</h4><p style="top:135px">No subscription or other maintenance contract, but one-time and sustainable repair work</p></div>
<div class="tile" style="left:748px;top:3676px"><div class="ti"><svg width="30" height="30" viewBox="0 0 30 30" fill="none" stroke="#fff" stroke-width="1.8"><path d="M15 7l2 4 4.5.6-3.3 3.1.8 4.5-4-2.1-4 2.1.8-4.5-3.3-3.1 4.5-.6z"/><path d="M6 23h18"/></svg></div><h4>First class service</h4><p>Our clients always come first!</p></div>
<a class="btn" style="left:469px;top:3932px;width:274px;height:43px;font-size:13px">Learn more about Lumavex</a>

<!-- contact -->
<div class="abs contact-photo" role="img" aria-label="Photo of a doctor working at a laptop in a bright clinic" style="z-index:-1"></div>
<svg class="abs" style="left:0;top:4018px" width="1200" height="100"><polygon points="0,0 450,92 880,0 1200,0 1200,-1 0,-1" fill="#1c2b3c"/></svg>
<h2 class="abs help-h">HOW CAN WE <em>HELP YOU?</em></h2>
<div class="field" style="top:4257px;height:49px"><svg viewBox="0 0 14 14"><circle cx="7" cy="4" r="3" fill="#9aa5b1"/><path d="M1 14c0-4 3-6 6-6s6 2 6 6z" fill="#9aa5b1"/></svg>First name</div>
<div class="field" style="top:4315px;height:49px"><svg viewBox="0 0 14 14"><path d="M3 1c-1.5.5-2 2-1.3 4 1 3 3.5 5.6 6.3 6.6 2 .7 3.3.2 4-1.2L9.8 8.6 8.4 9.6C7 8.9 5.8 7.7 5 6.3l1-1.4z" fill="#9aa5b1"/></svg>Phone number</div>
<div class="field" style="top:4372px;height:46px"><svg viewBox="0 0 14 14"><rect x="1" y="3" width="12" height="8" fill="none" stroke="#9aa5b1" stroke-width="1.4"/><path d="M1 3l6 5 6-5" fill="none" stroke="#9aa5b1" stroke-width="1.4"/></svg>Email address</div>
<div class="field" style="top:4430px;height:78px;align-items:flex-start;padding-top:22px;padding-left:22px">Comments</div>
<a class="btn" style="left:669px;top:4527px;width:147px;height:37px;font-size:11px">SUBMIT NOW</a>

<!-- footer -->
<footer class="abs footer">
  <div class="abs" style="left:100px;top:78px">
    <div class="brand" style="color:#fff">Lumavex<span class="dot" style="background:#fff"></span></div>
    <div class="tagline" style="color:#fff">Precision care for every scope</div>
  </div>
  <p class="abs" style="left:94px;top:172px;width:270px;font-size:12px;line-height:15px;opacity:.9">Lorem ipsum dolor sit amet, consectetur adipiscing elit, sed do eiusmod tempor incididunt ut labore et dolore</p>
  <div class="f-div" style="left:438px"></div>
  <div class="f-div" style="left:665px"></div>
  <div class="f-div" style="left:888px"></div>
  <div class="f-col" style="left:459px"><h5>NAVIGATION</h5><a>Home</a><a>Endoscope Repair</a><a>Used Endoscope</a><a>Endoscopy Systems</a></div>
  <div class="f-col" style="left:691px"><h5>RESOURCES</h5><a>Endoscopy Accesories</a><a>Purchase</a><a>Contact Us</a></div>
  <div class="f-col" style="left:904px"><h5>FOLLOW US</h5><div class="social"><i></i><i></i><i></i><i></i></div></div>
  <div class="abs" style="left:0;top:282px;width:1200px;height:1px;background:rgba(255,255,255,.35)"></div>
  <div class="abs" style="left:0;top:305px;width:1200px;text-align:center;font-size:12px">© 2022 Lumavex GmbH</div>
</footer>

</body>
</html>
```